DESIGN OF STATIONERY - TORVALE MED

WE WORK IN THE FIELD OF HEALTH (IMAGING: MRI - CT ETC.).
WE WOULD LIKE TO CREATE THE ENTIRE STATIONERY DESIGN : LETTERHEAD, BUSINESS CARD, CALENDAR, INVOICES, CD HOLDER, ETC.

Target Market(s)

PERSONS UNDERTAKING HEALTH EXAMINATIONS

```html
<!DOCTYPE html>
<html lang="en">
<head>
<meta charset="utf-8">
<title>Torvale Med — Stationery</title>
<link rel="stylesheet" href="https://fonts.googleapis.com/css2?family=Arimo:wght@400;700&display=swap">
<style>
  :root{
    --bg:#dcdcdc;
    --paper:#ffffff;
    --blue:#1f74bb;
    --blue-light:#4f98d6;
    --teal:#00a99d;
    --ink:#333333;
    --muted:#6b6b6b;
    --rule:#555555;
  }
  *{box-sizing:border-box;margin:0;padding:0}
  html,body{width:1200px;height:1200px;overflow:hidden;background:var(--bg);font-family:"Arimo",Arial,sans-serif;color:var(--ink)}
  .canvas{position:relative;width:1200px;height:1200px}
  .sheet{position:absolute;background:var(--paper);overflow:hidden;box-shadow:2px 3px 6px rgba(0,0,0,.25)}

  /* brand name */
  .brand{position:absolute;font-weight:700;color:var(--blue);white-space:nowrap;display:flex;align-items:center;gap:6px}
  .brand .dot{width:9px;height:9px;border-radius:50%;background:var(--teal)}

  /* footer band */
  .footer-line{position:absolute;left:0;height:3px;background:var(--teal)}
  .footer-dot{position:absolute;width:7px;height:7px;border-radius:50%;background:var(--teal)}
  .footer-band{position:absolute;left:0;right:0;bottom:0;background:var(--blue);color:#fff;text-align:center;display:flex;align-items:center;justify-content:center}

  /* contacts */
  .contacts{position:absolute;list-style:none;color:var(--muted)}
  .contacts li{display:flex;align-items:center;gap:6px;white-space:nowrap}
  .contacts svg{fill:var(--teal);flex:none}

  /* business card front */
  .card-front{left:168px;top:84px;width:414px;height:238px}
  .card-front .brand{left:28px;top:96px;font-size:21px}
  .card-front .divider{position:absolute;left:206px;top:72px;width:1px;height:82px;background:var(--rule)}
  .card-front .person{position:absolute;left:221px;top:72px}
  .person .name{font-size:14.5px;font-weight:700;color:var(--teal);letter-spacing:.2px}
  .person .role{font-size:11px;color:var(--muted);margin-top:1px}
  .card-front .contacts{left:221px;top:108px;font-size:11.5px;line-height:16.5px}
  .card-front .footer-line{top:208px;width:380px}
  .card-front .footer-dot{left:377px;top:206px}
  .card-front .footer-band{height:26px;font-size:11.5px}

  /* business card back */
  .card-back{left:618px;top:84px;width:414px;height:238px;background:var(--blue)}
  .card-back .brand{left:0;right:0;top:100px;justify-content:center;font-size:32px;color:var(--blue-light)}
  .card-back .brand .dot{background:var(--blue-light);width:12px;height:12px}

  /* page header */
  .page-header .brand{left:48px;top:48px;font-size:20px}
  .page-header .contacts{left:398px;top:28px;font-size:8.5px;line-height:13px}
  .page-header .rule-thick{position:absolute;left:0;right:0;top:72px;height:5px;background:var(--teal)}
  .page-header .rule-thin{position:absolute;left:0;right:0;top:80px;height:1.5px;background:var(--blue)}
  .page .footer-line{top:725px;width:505px}
  .page .footer-dot{left:500px;top:723px}
  .page .footer-band{height:22px;font-size:8.5px}

  /* letterhead */
  .letterhead{left:50px;top:362px;width:533px;height:753px}
  .letter{position:absolute;left:49px;top:230px;width:436px}
  .letter .salutation{font-size:12px;font-weight:700;color:#444;margin-bottom:21px}
  .letter p{font-size:8.3px;line-height:11px;color:#555;margin-bottom:10px}
  .letter .closing{font-size:6.5px;font-weight:700;color:#444;margin-top:16px}
  .letter .signature{width:90px;height:26px;margin-top:18px;background:linear-gradient(90deg,#e6e6e6,#f2f2f2)}

  /* invoice */
  .invoice{left:618px;top:362px;width:534px;height:753px}
  .invoice-head{position:absolute;left:51px;top:120px}
  .invoice-head h1{font-size:29px;font-weight:700;color:var(--teal);letter-spacing:.5px;margin-bottom:11px}
  .invoice-head dl{font-size:11px;font-weight:700;line-height:16.5px}
  .invoice-head dt{display:inline;color:var(--teal)}
  .invoice-head dd{display:inline;color:var(--ink)}
  .invoice-head dd::after{content:"";display:block}
  .items{position:absolute;left:53px;top:239px;width:428px;border-collapse:collapse}
  .items th{background:var(--blue);color:#fff;font-size:10.5px;font-weight:700;height:28px;text-align:left;padding-left:14px;border-right:1px solid #fff}
  .items th:last-child{border-right:none;padding-left:7px}
  .items th.center{text-align:center;padding-left:0}
  .items td{border:1px solid #444;height:43px;font-weight:700;color:var(--ink)}
  .items td.sl{text-align:center;font-size:13px;width:34px}
  .items td.desc{width:203px}
  .items td.price{font-size:8px;text-align:center;width:63px}
  .items td.qty{text-align:center;font-size:13px;width:62px}
  .summary{position:absolute;left:291px;top:596px;width:190px;border-collapse:collapse}
  .summary td{border:1px solid #444;height:35px;font-size:8px;font-weight:700;text-align:center}
  .summary td:first-child{width:63px}
</style>
</head>
<body>
<div class="canvas">

  <svg width="0" height="0" style="position:absolute" aria-hidden="true">
    <symbol id="i-phone" viewBox="0 0 16 16"><path d="M3.6 1.5l2.2-.3 1.4 3.3-1.6 1.1c.8 1.8 2 3 3.8 3.8l1.1-1.6 3.3 1.4-.3 2.2c-.2 1-1.1 1.6-2 1.5C6.6 12.4 2.1 7.9 1.6 3.5c-.1-1 .5-1.8 2-2z"/></symbol>
    <symbol id="i-mail" viewBox="0 0 16 16"><path d="M1 3h14v10H1zM2.2 4.2v.3L8 8.6l5.8-4.1v-.3zM2.2 6v5.8h11.6V6L8 10.1z"/></symbol>
    <symbol id="i-web" viewBox="0 0 16 16"><path d="M8 1a7 7 0 1 0 0 14A7 7 0 0 0 8 1zm0 1.6c.6.7 1.1 1.9 1.4 3.4H6.6C6.9 4.5 7.4 3.3 8 2.6zM2.9 9.6A5.5 5.5 0 0 1 2.9 6.4h2.2a12 12 0 0 0 0 3.2zm3.7 0a10 10 0 0 1 0-3.2h2.8a10 10 0 0 1 0 3.2zm4.3 0a12 12 0 0 0 0-3.2h2.2a5.5 5.5 0 0 1 0 3.2zM8 13.4c-.6-.7-1.1-1.9-1.4-3.4h2.8c-.3 1.5-.8 2.7-1.4 3.4z"/></symbol>
  </svg>

  <!-- Business card, front -->
  <section class="sheet card-front">
    <div class="brand"><span class="dot"></span>TORVALE MED</div>
    <div class="divider"></div>
    <div class="person">
      <div class="name">DANIEL HARLOW</div>
      <div class="role">Manager</div>
    </div>
    <ul class="contacts">
      <li><svg width="10" height="10"><use href="#i-phone"/></svg>555-014-2100</li>
      <li><svg width="10" height="10"><use href="#i-mail"/></svg>hello@torvalemed.example</li>
      <li><svg width="10" height="10"><use href="#i-web"/></svg>www.torvalemed.example</li>
    </ul>
    <div class="footer-line"></div>
    <div class="footer-dot"></div>
    <div class="footer-band">Your Address, City, State, Zip 0000</div>
  </section>

  <!-- Business card, back -->
  <section class="sheet card-back">
    <div class="brand"><span class="dot"></span>TORVALE MED</div>
  </section>

  <!-- Letterhead -->
  <section class="sheet page letterhead">
    <header class="page-header">
      <div class="rule-thick"></div>
      <div class="rule-thin"></div>
      <div class="brand"><span class="dot"></span>TORVALE MED</div>
      <ul class="contacts">
        <li><svg width="8" height="8"><use href="#i-phone"/></svg>555-014-2100</li>
        <li><svg width="8" height="8"><use href="#i-mail"/></svg>hello@torvalemed.example</li>
        <li><svg width="8" height="8"><use href="#i-web"/></svg>www.torvalemed.example</li>
      </ul>
    </header>
    <article class="letter">
      <div class="salutation">Dear Mr. Harlow,</div>
      <p>Lorem ipsum dolor sit amet, consectetuer adipiscing elit, sed diam nonummy nibh euismod tincidunt ut laoreet dolore magna aliquam erat volutpat. Ut wisi enim ad minim veniam, quis nostrud exerci tation ullamcorper suscipit lobortis nisl ut aliquip ex ea commodo consequat. Duis autem vel eum iriure dolor in hendrerit in vulputate velit esse molestie consequat, vel illum dolore eu feugiat</p>
      <p>Lorem ipsum dolor sit amet, consectetuer adipiscing elit, sed diam nonummy nibh euismod tincidunt ut laoreet dolore magna aliquam erat volutpat. Ut wisi enim ad minim veniam, quis nostrud exerci tation ullamcorper suscipit lobortis nisl ut aliquip ex ea commodo consequat. Duis autem vel eum iriure dolor in hendrerit in vulputate velit esse molest</p>
      <p>Lorem ipsum dolor sit amet, consectetuer adipiscing elit, sed diam nonummy nibh euismod tincidunt ut laoreet dolore magna aliquam erat volutpat. Ut wisi enim ad minim veniam, quis nostrud exerci tation ullamcorper suscipit lobortis nisl ut aliquip ex ea commodo consequat. Duis autem vel eum iriure dolor in hendrerit in suscipit lobortis nisl ut aliquip ex ea commodo consequat. Duis autem vel eum iriure dolor in hendrerit in vulputate velit esse molestie consequat, vel illum</p>
      <p>Lorem ipsum dolor sit amet, consectetuer adipiscing elit, sed diam nonummy nibh euismod tincidunt ut laoreet dolore magna aliquam erat volutpat. Ut wisi enim ad minim veniam, quis nostrud exerci tation ullamcorper suscipit lobortis nisl ut aliquip ex ea commodo consequat. Duis autem vel eum iriure dolor in</p>
      <div class="closing">Sincerely,</div>
      <div class="signature" role="img" aria-label="Handwritten signature"></div>
    </article>
    <div class="footer-line"></div>
    <div class="footer-dot"></div>
    <div class="footer-band">Your Address, City, State, Zip 0000</div>
  </section>

  <!-- Invoice -->
  <section class="sheet page invoice">
    <header class="page-header">
      <div class="rule-thick"></div>
      <div class="rule-thin"></div>
      <div class="brand"><span class="dot"></span>TORVALE MED</div>
      <ul class="contacts">
        <li><svg width="8" height="8"><use href="#i-phone"/></svg>555-014-2100</li>
        <li><svg width="8" height="8"><use href="#i-mail"/></svg>hello@torvalemed.example</li>
        <li><svg width="8" height="8"><use href="#i-web"/></svg>www.torvalemed.example</li>
      </ul>
    </header>
    <div class="invoice-head">
      <h1>INVOICE</h1>
      <dl>
        <dt>BANK ACCOUNT:</dt> <dd>02345678124</dd>
        <dt>VAT:</dt> <dd>0234567</dd>
        <dt>DATE:</dt> <dd>30.05.2023</dd>
      </dl>
    </div>
    <table class="items">
      <thead>
        <tr><th class="center">SL.</th><th>ITEM DESCRIPTION</th><th class="center">PRICE</th><th class="center">QTY.</th><th>TOTAL</th></tr>
      </thead>
      <tbody>
        <tr><td class="sl">1</td><td class="desc"></td><td class="price">$00.00</td><td class="qty">1</td><td></td></tr>
        <tr><td class="sl">2</td><td class="desc"></td><td class="price">$00.00</td><td class="qty">2</td><td></td></tr>
        <tr><td class="sl">3</td><td class="desc"></td><td class="price">$00.00</td><td class="qty">1</td><td></td></tr>
        <tr><td class="sl">4</td><td class="desc"></td><td class="price">$00.00</td><td class="qty">2</td><td></td></tr>
        <tr><td class="sl">5</td><td class="desc"></td><td class="price">$00.00</td><td class="qty">1</td><td></td></tr>
        <tr><td class="sl">6</td><td class="desc"></td><td class="price">$00.00</td><td class="qty">1</td><td></td></tr>
      </tbody>
    </table>
    <table class="summary">
      <tr><td>SUB TOTAL</td><td></td></tr>
      <tr><td>TAX</td><td></td></tr>
      <tr><td>TOTAL</td><td></td></tr>
    </table>
    <div class="footer-line"></div>
    <div class="footer-dot"></div>
    <div class="footer-band">Your Address, City, State, Zip 0000</div>
  </section>

</div>
</body>
</html>
```